Business Card Design

New business card design

Target Market(s)

Residential & Commercial Property Managers

Industry/Entity Type

Plumbing Services

Contact Information for Business Card

Name - Rowan Keddle, title - Director, Phone Number - 0431 286 517, email - rowan@tbk-plumbing.com.au, Company ABN - 73 215 904 386,

Font styles to use
Sans Serif

Colors
0054AA
0677BA
7BADD7
CADEEF
E8F1F8

```html
<!DOCTYPE html>
<html lang="en">
<head>
<meta charset="utf-8">
<title>TBK Plumbing Services – Business Card</title>
<link rel="stylesheet" href="https://fonts.googleapis.com/css2?family=Montserrat:wght@400;500;700&display=swap">
<style>
  :root {
    --backdrop: #171819;
    --card-light: #f4f4f4;
    --card-dark: #1d232a;
    --ink: #1d232a;
    --brand-blue: #29a3da;
    --muted: #5a5f63;
    --white: #ffffff;
  }
  * { margin: 0; padding: 0; box-sizing: border-box; }
  html, body {
    width: 1200px; height: 1059px; overflow: hidden;
    background: var(--backdrop);
    font-family: "Montserrat", sans-serif;
  }
  .canvas { position: relative; width: 1200px; height: 1059px; }
  .card {
    position: absolute; width: 690px; height: 392px;
    border-radius: 16px; overflow: hidden;
  }
  .card--front { left: 256px; top: 89px; background: var(--card-light); }
  .card--back { left: 254px; top: 547px; background: var(--card-dark); }

  .wordmark {
    position: absolute; font-weight: 500; letter-spacing: 6px; line-height: 1;
  }
  .tagline {
    position: absolute; font-weight: 400; text-transform: lowercase; line-height: 1;
  }
  .card--front .wordmark { left: 42px; top: 52px; font-size: 66px; color: var(--ink); }
  .card--front .tagline { left: 46px; top: 137px; font-size: 10px; letter-spacing: 9.6px; color: var(--muted); }
  .card--back .wordmark { left: 0; right: 0; top: 100px; text-align: center; font-size: 104px; letter-spacing: 10px; color: var(--white); }
  .card--back .tagline { left: 0; right: 0; top: 245px; text-align: center; font-size: 14px; letter-spacing: 16px; padding-left: 16px; color: var(--white); }

  .accent-tab { position: absolute; left: 0; top: 199px; width: 19px; height: 40px; background: var(--brand-blue); }
  .name { position: absolute; left: 43px; top: 193px; font-size: 27px; font-weight: 700; color: var(--brand-blue); }
  .role { position: absolute; left: 43px; top: 224px; font-size: 17px; font-weight: 400; color: var(--ink); }
  .abn { position: absolute; left: 43px; top: 260px; font-size: 17px; color: var(--ink); }
  .abn span { color: var(--brand-blue); }
  .contact { position: absolute; left: 43px; top: 302px; list-style: none; font-size: 17px; color: var(--ink); }
  .contact li { display: flex; align-items: center; gap: 8px; height: 26px; }
  .contact svg { width: 13px; height: 13px; fill: var(--brand-blue); }
  .footer-band { position: absolute; left: 0; bottom: 0; width: 690px; height: 16px; }
</style>
</head>
<body>
<main class="canvas">
  <section class="card card--front" aria-label="Business card front">
    <div class="wordmark">tbk</div>
    <div class="tagline">plumbing services</div>
    <div class="accent-tab"></div>
    <h1 class="name">Rowan Keddle</h1>
    <p class="role">Director</p>
    <p class="abn"><span>Company ABN</span> - 73 215 904 386</p>
    <ul class="contact">
      <li>
        <svg viewBox="0 0 24 24" aria-hidden="true"><path d="M6.6 10.8a15.1 15.1 0 0 0 6.6 6.6l2.2-2.2a1 1 0 0 1 1-.25 11.4 11.4 0 0 0 3.6.57 1 1 0 0 1 1 1V20a1 1 0 0 1-1 1A17 17 0 0 1 3 4a1 1 0 0 1 1-1h3.5a1 1 0 0 1 1 1c0 1.25.2 2.45.57 3.57a1 1 0 0 1-.25 1z"/></svg>
        0431 286 517
      </li>
      <li>
        <svg viewBox="0 0 24 24" aria-hidden="true"><path d="M2 5h20v14H2z M2 5l10 8 10-8" fill="var(--brand-blue)" stroke="#f4f4f4" stroke-width="1.5"/></svg>
        rowan@tbk-plumbing.com.au
      </li>
    </ul>
    <svg class="footer-band" viewBox="0 0 690 16" preserveAspectRatio="none" aria-hidden="true">
      <polygon points="0,0 338,0 322,16 0,16" fill="var(--card-dark)"/>
      <polygon points="356,0 690,0 690,16 334,16" fill="var(--brand-blue)"/>
    </svg>
  </section>

  <section class="card card--back" aria-label="Business card back">
    <div class="wordmark">tbk</div>
    <div class="tagline">plumbing services</div>
  </section>
</main>
</body>
</html>
```